Design my site www.brieflyledger.com

So here is what I am thinking in terms of design:

https://plenvo.com

https://www.skyluxair.com

http://kalvex.com/harbor-plaza-tower/

I want the theme to be white and blue (royal blue). I attached a paint picture of what I would like the site to look like in terms of placing the text. Generally, what I like about the sites above is that they are simple, you can navigate easily and have some kind of idea of what's going on by looking at the center (picture and motto). Let's establish a clear understanding of how the functional part of the site would look like. Please see the picture attached.

I want to keep it simple: On top would be the Name 'BRIEFLY ledger", somewhere to the right on top on the page would be 'Sign in" button.

In the center would be a picture (maybe a video) with the Motto (on top of it all in capital) OBSERVE NAVIGATE DECIDE and below would be the "sign up now"

Below the picture (like on kalvex.com site) or to the left on top of the page would be "About Us', "Press" "Contact Us' buttons.

Then once the user gets to his page his got 3 tabs " Press Headlines", "Events", " Briefings".

we would keep the same format I only have on the site, but separate for every Tab.

I do not want the user to get distracted. I also want him to be able to access the page though mobile phone and be able to get automatic updates just like Zorvan Pings without having to sign in daily.

The landing page must be minimalist yet with business/corporate feel where users can navigate easily and a "what you see is what you get" approach. You want an image or video (personally I prefer the video.. it does capture the users attention instantly, as long as it is an interesting video), with your taglines in it.

Sections available to public: About Us, Contact Us, Landing Page with Signup Option

Private: Public Sections + User Account Page, Tabs for (Events, Press Headlines, Briefings)

Target Market(s)

PR/media monitoring/diplomatic community

Coding

Coded - Design and coding required

Number of Pages Required

1 page

Font styles to use
Serif
Sans Serif

Colors
0255a3
ec1f27

Requirements
Must have
• a simple landing page, that is user friendly.
Nice to have
• a video with the explanation of how to navigate the site
Should not have
• too many colors, graphs etc.

```html
<!DOCTYPE html>
<html lang="en">
<head>
<meta charset="utf-8">
<title>BRIEFLY ledger — Events</title>
<link rel="stylesheet" href="https://fonts.googleapis.com/css2?family=Open+Sans:wght@400;600&display=swap">
<style>
  :root {
    --royal-blue: #0255a3;
    --signal-red: #ec1f27;
    --panel-grey: #e4e4e4;
    --divider: #a8a8a8;
    --ink: #1a1a1a;
    --ink-soft: #7a7a7a;
    --ink-mid: #444444;
    --white: #ffffff;
  }
  * { box-sizing: border-box; margin: 0; padding: 0; }
  html, body {
    width: 1200px;
    height: 600px;
    overflow: hidden;
    background: var(--white);
    font-family: "Open Sans", Arial, sans-serif;
  }
  .dashboard {
    position: relative;
    width: 1200px;
    height: 600px;
  }

  /* Section tabs */
  .tab {
    position: absolute;
    left: 161px;
    width: 247px;
    height: 126px;
    display: flex;
    align-items: center;
    justify-content: center;
    background: var(--royal-blue);
    color: var(--white);
    font-size: 14.5px;
    letter-spacing: 0.2px;
    text-transform: uppercase;
    text-decoration: none;
  }
  .tab--headlines { top: 105px; }
  .tab--briefings { top: 377px; }

  .tab-active-frame {
    position: absolute;
    left: 161px;
    top: 241px;
    width: 259px;
    height: 126px;
    background: var(--panel-grey);
  }
  .tab--events {
    top: 248px;
    left: 167px;
    width: 241px;
    height: 111px;
    background: var(--signal-red);
  }
  .tab-pointer {
    position: absolute;
    left: 407px;
    top: 285px;
    width: 20px;
    height: 38px;
  }

  /* Event list */
  .event-panel {
    position: absolute;
    left: 470px;
    top: 105px;
    width: 568px;
    height: 398px;
    background: var(--panel-grey);
  }
  .event {
    display: grid;
    grid-template-columns: 100px 70px 1fr;
    padding: 0 20px 0 24px;
  }
  .event + .event { border-top: 1px dotted var(--divider); }
  .event:nth-child(1) { height: 132px; padding-top: 48px; }
  .event:nth-child(2) { height: 113px; padding-top: 22px; }
  .event:nth-child(3) { padding-top: 16px; }

  .event-date {
    font-size: 12.5px;
    line-height: 16px;
    color: var(--ink);
  }
  .event-time {
    font-size: 12.5px;
    line-height: 16px;
    color: var(--ink);
  }
  .event-venue {
    display: block;
    margin-top: 3px;
    font-size: 10.5px;
    line-height: 16px;
    color: var(--ink-mid);
  }
  .event-title {
    font-size: 13px;
    line-height: 16px;
    font-weight: 400;
    color: var(--ink);
  }
  .event-summary {
    margin-top: 3px;
    font-size: 10.3px;
    line-height: 16px;
    color: var(--ink-soft);
  }

  .read-more {
    position: absolute;
    left: 480px;
    top: 353px;
    font-size: 12.5px;
    line-height: 16px;
    color: var(--signal-red);
    text-decoration: none;
    border-bottom: 1.5px solid var(--signal-red);
    padding-bottom: 1px;
  }
</style>
</head>
<body>
  <main class="dashboard">
    <nav aria-label="Account sections">
      <a class="tab tab--headlines" href="#">Newspapers Headlines</a>
      <div class="tab-active-frame"></div>
      <a class="tab tab--events" href="#" aria-current="page">Events</a>
      <svg class="tab-pointer" viewBox="0 0 20 38" aria-hidden="true">
        <polygon points="0,0 19,19 0,38" fill="var(--signal-red)"/>
      </svg>
      <a class="tab tab--briefings" href="#">Daily Briefing</a>
    </nav>

    <section class="event-panel" aria-label="Events">
      <article class="event">
        <p class="event-date">Jan 05, 2016</p>
        <p class="event-time">Time<span class="event-venue">Venue</span></p>
        <div>
          <h3 class="event-title">Lorem ipsum dolor sit amet, consetetur sadipscing elitr</h3>
          <p class="event-summary">Duis autem vel eum iriure dolor in hendrerit in vulputate velit esse molestie vel illum dolore eu feugiat nulla facilisis at vero eros et accumsan et iusto odio dignissim qui blandit praesent luptatum zzril delenit augue duis dolore.</p>
        </div>
      </article>
      <article class="event">
        <p class="event-date">Jan 05, 2016</p>
        <p class="event-time">Time<span class="event-venue">Venue</span></p>
        <div>
          <h3 class="event-title">Lorem ipsum dolor sit amet, consetetur sadipscing elitr</h3>
          <p class="event-summary">Duis autem vel eum iriure dolor in hendrerit in vulputate velit esse molestie vel illum dolore eu feugiat nulla facilisis at vero eros et accumsan et iusto odio dignissim qui blandit praesent luptatum zzril delenit augue duis dolore.</p>
        </div>
      </article>
      <article class="event">
        <p class="event-date">Jan 05, 2016</p>
        <p class="event-time">Time<span class="event-venue">Venue</span></p>
        <div>
          <h3 class="event-title">Lorem ipsum dolor sit amet, consetetur sadipscing elitr</h3>
          <p class="event-summary">Duis autem vel eum iriure dolor in hendrerit in vulputate velit esse molestie vel illum dolore eu feugiat nulla facilisis at vero eros et accumsan et iusto odio dignissim qui blandit praesent luptatum zzril delenit augue duis dolore.</p>
        </div>
      </article>
      <a class="read-more" href="#">Read More</a>
    </section>
  </main>
</body>
</html>
```